creation of a business card design for a company specializing in the creation...

I would like to create a design for a professional business card on a black background and with the company's colors (I am attaching some files: including the logo in horizontal and centered format, I am also attaching a recent project design a T-shirt, this is the one I chose to give you an idea of my preferences.

we are in the process of developing a new website design, it is still in the development phase but it can be viewed at the following address: www.vantrelmo.be to give you other ideas about the company
you will see for yourself the subject of my main activity: company specializing in the construction of stairs

I would like a business card that stands out from the rest with a unique design

here is the informations
Name: Lucien Barthel
Function: Manager
Address: Rue Moulinet du Parc 42
7180 La Louvière
telephone: +32 468 219 804
email: info@rx7p.be
website: rx7p. be
social networks: Facebook, YouTube, TikTok, Instagram

Target Market(s)

customer who wants to have a beautiful staircase built

Industry/Entity Type

contruction d'escalier

Contact Information for Business Card

Adresse. Numero de telephone, site web, le texte : "Createur d'escalier", logo recto-verso, icone des reseaux sociaux

Requirements
Must have
• the mention: Stair creator
Nice to have
• an illustration of a designer staircase
Should not have
• do not distort the logo

```html
<!DOCTYPE html>
<html lang="fr">
<head>
<meta charset="utf-8">
<title>RX7P – Business card</title>
<link rel="stylesheet" href="https://fonts.googleapis.com/css2?family=Michroma&family=Oswald:wght@600&family=Poppins:wght@400;500&display=swap">
<style>
  :root {
    --backdrop: #8a8a8a;
    --card: #121212;
    --blue: #5f93b5;
    --blue-light: #a3c4d9;
    --blue-deep: #2a5a76;
    --white: #ffffff;
  }
  html, body { margin: 0; padding: 0; }
  body {
    width: 1093px; height: 1200px; overflow: hidden;
    background: var(--backdrop);
    font-family: "Poppins", sans-serif;
    position: relative;
  }
  .card {
    position: absolute; left: 258px;
    width: 578px; height: 357px;
    background: var(--card);
    border-radius: 27px;
    overflow: hidden;
    color: var(--white);
  }
  .card--front { top: 226px; }
  .card--back { top: 620px; }
  .card__band {
    position: absolute; left: 0; right: 0; bottom: 0; height: 9px;
    background: var(--blue);
  }
  .card--back .card__band { background: var(--blue-light); }

  .holder { position: absolute; left: 32px; top: 62px; }
  .holder__name {
    font-family: "Michroma", sans-serif; font-size: 19px;
    color: var(--blue); letter-spacing: 0.5px; margin: 0; line-height: 1.1;
  }
  .holder__role { font-size: 16px; margin: 0; line-height: 1.2; }

  .brand { position: absolute; right: 34px; top: 150px; text-align: right; }
  .brand__name {
    font-size: 48px; font-weight: 500; letter-spacing: 6px;
    line-height: 1; margin: 0; margin-right: -6px;
  }
  .brand__tagline {
    font-size: 10.5px; font-weight: 500; letter-spacing: 4.6px;
    color: var(--blue); margin: 8px -4.6px 0 0;
  }

  .contacts { position: absolute; left: 32px; top: 252px; margin: 0; padding: 0; list-style: none; }
  .contacts li { display: flex; align-items: center; gap: 8px; font-size: 17px; line-height: 21px; }
  .contacts svg { width: 15px; height: 15px; fill: none; stroke: var(--blue); stroke-width: 1.6; }

  .address { position: absolute; right: 34px; top: 279px; text-align: right; font-size: 17px; line-height: 21px; font-style: normal; }

  .motto {
    position: absolute; left: 0; right: 0; top: 50px; margin: 0;
    text-align: center;
    font-family: "Oswald", sans-serif; font-weight: 600; font-size: 17px;
    letter-spacing: 1px; line-height: 1;
  }
  .badge {
    position: absolute; left: 204px; top: 76px; width: 170px; height: 134px;
    border-radius: 50%;
    background: radial-gradient(circle at 50% 45%, #2f6684 0%, var(--blue-deep) 45%, #16303f 100%);
  }
  .back-brand { position: absolute; left: 0; right: 0; top: 216px; text-align: center; }
  .back-brand__name { font-size: 38px; font-weight: 500; letter-spacing: 5px; margin: 0 -5px 0 0; line-height: 1; }
  .back-brand__tagline { font-size: 10.5px; font-weight: 500; letter-spacing: 3px; color: var(--blue); margin: 8px 0 0; }

  .socials { position: absolute; left: 0; right: 0; top: 288px; display: flex; justify-content: center; gap: 6px; margin: 0; padding: 0; list-style: none; }
  .socials li { width: 25px; height: 25px; border: 1.3px solid var(--blue); border-radius: 50%; }
</style>
</head>
<body>
  <section class="card card--front">
    <div class="holder">
      <p class="holder__name">LUCIEN BARTHEL</p>
      <p class="holder__role">Manager</p>
    </div>
    <div class="brand">
      <p class="brand__name">RX7P</p>
      <p class="brand__tagline">ORIGINAL STAIRCASES</p>
    </div>
    <ul class="contacts">
      <li><svg viewBox="0 0 16 16"><path d="M4 2l2.5 3-1.5 1.5c1 2 2.5 3.5 4.5 4.5L11 9.5l3 2.5-1.5 2C7 14 2 9 2 3.5z"/></svg>+32 468 219 804</li>
      <li><svg viewBox="0 0 16 16"><rect x="1.5" y="3.5" width="13" height="9"/><path d="M1.5 3.5L8 9l6.5-5.5"/></svg>info@rx7p.be</li>
      <li><svg viewBox="0 0 16 16"><circle cx="8" cy="8" r="6.5"/><ellipse cx="8" cy="8" rx="3" ry="6.5"/><path d="M1.5 8h13"/></svg>www.rx7p. be</li>
    </ul>
    <address class="address">Rue Moulinet du Parc 42<br>7180 La Louvière</address>
    <div class="card__band"></div>
  </section>

  <section class="card card--back">
    <p class="motto">CRÉATEUR D'ESCALIER</p>
    <div class="badge" role="img" aria-label="Round badge illustration of a floating designer staircase"></div>
    <div class="back-brand">
      <p class="back-brand__name">RX7P</p>
      <p class="back-brand__tagline">ORIGINAL STAIRCASES</p>
    </div>
    <ul class="socials" aria-label="Social networks">
      <li></li><li></li><li></li><li></li>
    </ul>
    <div class="card__band"></div>
  </section>
</body>
</html>
```